Create a new business card

I’m looking to update my business card to make it match the rest of my brand. I will include my current website as well as what my vehicle designs look like, etc..
What my business currently services
Weekly maintenance pool openings / closings
Equipment repair, including pumps, heaters, salt systems, filters, etc.
We install automatic covers and maintain them as well as provide preventative maintenance

I would like to include my name.
Dorian Pelkin.
My title
Owner
My email
Dorian@tidewellnx.com
4015827160
Www.tidewellnx.com

```html
<!DOCTYPE html>
<html lang="en">
<head>
<meta charset="utf-8">
<title>Tidewell Pool Service – Business Card</title>
<link href="https://fonts.googleapis.com/css2?family=Roboto:wght@400;700&display=swap" rel="stylesheet">
<style>
  :root {
    --backdrop: #c9c9cb;
    --card-white: #ffffff;
    --sky: #2ab0e8;
    --ocean: #1f6fc0;
    --deep: #173a85;
    --navy: #2c3c78;
    --ink: #4a4a4a;
    --muted: #6d6d6d;
    --rule: #b8b8b8;
  }
  * { box-sizing: border-box; margin: 0; padding: 0; }
  html, body { width: 1200px; height: 876px; overflow: hidden; }
  body {
    background: var(--backdrop);
    font-family: "Roboto", Arial, sans-serif;
    display: flex;
    align-items: center;
    justify-content: center;
    gap: 40px;
  }
  .card {
    width: 540px;
    height: 309px;
    border-radius: 22px;
    position: relative;
    overflow: hidden;
  }
  /* Front */
  .card--front {
    background: var(--card-white);
    display: flex;
    align-items: center;
  }
  .front__brand {
    width: 46%;
    display: flex;
    flex-direction: column;
    align-items: center;
    gap: 10px;
  }
  .brand-mark {
    width: 22px; height: 22px; border-radius: 50%;
    background: var(--sky);
  }
  .brand-name {
    font-weight: 700;
    font-size: 26px;
    color: var(--navy);
    text-align: center;
    line-height: 1.15;
  }
  .front__divider {
    width: 1px;
    height: 140px;
    background: var(--rule);
  }
  .front__details {
    padding-left: 26px;
  }
  .person-name {
    font-weight: 700;
    font-size: 24px;
    color: var(--sky);
    text-transform: uppercase;
    letter-spacing: 0.3px;
  }
  .person-title {
    font-size: 17px;
    color: var(--muted);
    margin-top: 2px;
  }
  .contact-list {
    list-style: none;
    margin-top: 26px;
    display: flex;
    flex-direction: column;
    gap: 6px;
  }
  .contact-item {
    display: flex;
    align-items: center;
    gap: 10px;
    font-size: 17px;
    color: var(--ink);
  }
  .contact-icon { width: 14px; height: 14px; flex: none; }
  /* Back */
  .card--back {
    display: flex;
    align-items: center;
    justify-content: center;
  }
  .back__pattern {
    position: absolute; inset: 0;
    background: linear-gradient(135deg, var(--sky) 0%, var(--ocean) 50%, var(--deep) 100%);
  }
  .back__brand {
    position: relative;
    width: 200px; height: 200px;
    border-radius: 50%;
    background: var(--card-white);
    display: flex;
    flex-direction: column;
    align-items: center;
    justify-content: center;
    gap: 8px;
  }
  .back__brand .brand-name { font-size: 28px; }
</style>
</head>
<body>

  <section class="card card--front" aria-label="Business card front">
    <div class="front__brand">
      <span class="brand-mark"></span>
      <p class="brand-name">Tidewell<br>Pool Service</p>
    </div>
    <div class="front__divider"></div>
    <div class="front__details">
      <h1 class="person-name">Dorian Pelkin</h1>
      <p class="person-title">Owner</p>
      <ul class="contact-list">
        <li class="contact-item">
          <svg class="contact-icon" viewBox="0 0 16 16"><circle cx="8" cy="8" r="8" fill="#2ab0e8"/><path d="M5.2 4.2l1.4-.4.9 2-1 .8a5 5 0 0 0 2.2 2.2l.8-1 2 .9-.4 1.4c-3 .5-6.6-3.1-5.9-5.9z" fill="#fff"/></svg>
          4015827160
        </li>
        <li class="contact-item">
          <svg class="contact-icon" viewBox="0 0 16 16"><circle cx="8" cy="8" r="8" fill="#2ab0e8"/><rect x="3.8" y="5" width="8.4" height="6" fill="#fff"/><path d="M3.8 5l4.2 3.4L12.2 5" fill="none" stroke="#2ab0e8" stroke-width="1"/></svg>
          Dorian@tidewellnx.com
        </li>
        <li class="contact-item">
          <svg class="contact-icon" viewBox="0 0 16 16"><circle cx="8" cy="8" r="8" fill="#2ab0e8"/><circle cx="8" cy="8" r="4" fill="none" stroke="#fff" stroke-width="1.2"/><path d="M4 8h8M8 4c-2 2.5-2 5.5 0 8M8 4c2 2.5 2 5.5 0 8" fill="none" stroke="#fff" stroke-width="1"/></svg>
          www.tidewellnx.com
        </li>
      </ul>
    </div>
  </section>

  <section class="card card--back" aria-label="Business card back">
    <div class="back__pattern" role="img" aria-label="Blue water splash texture background"></div>
    <div class="back__brand">
      <span class="brand-mark"></span>
      <p class="brand-name">Tidewell<br>Pool Service</p>
    </div>
  </section>

</body>
</html>
```